Brook Refrigeration. Refrigeration and air conditioning specialists.

We need a website to promote our business. We would a modern simple design using the colours from our logo and black. We want it to be fun but proffesional.

Target Market(s)

Commercial

Number of Pages Required

4 page

Requirements
Must have
• Home Page, About Us, Services and Contact Us.
• 24/7 365 days service available.
• Brook Refrigeration's dedicated team specialises in commercial refrigeration and air conditioning equipment.
• Based in Harbourton, we cover Northvale Metro and surrounding areas.
Nice to have
• KNOWLEDGE . EXPERIENCE . PASSION in bold.
• Our experienced and highly trained technicians provide extensive knowledge and exceptional skills for your commercial refrigeration and air conditioning requirements.
• Pictures of commercial refrigeration.
Should not have
• No mention of domestic services.

```html
<!DOCTYPE html>
<html lang="en">
<head>
<meta charset="utf-8">
<title>Brook Refrigeration</title>
<link href="https://fonts.googleapis.com/css2?family=Roboto:wght@300;400;500;700;900&family=Roboto+Condensed:wght@300;400;700&display=swap" rel="stylesheet">
<style>
:root{
  --purple:#40275e;
  --purple-deep:#3a2455;
  --purple-nav:#4a2f6b;
  --green:#a4ef68;
  --ink:#222222;
  --text:#333333;
  --muted:#666666;
  --line:#b9b9b9;
  --white:#ffffff;
  --grey-bar:#555555;
}
*{box-sizing:border-box;margin:0;padding:0}
html,body{width:1200px;height:3789px;overflow:hidden}
body{position:relative;background:var(--white);font-family:"Roboto",Arial,sans-serif;color:var(--text)}
.abs{position:absolute}

/* header */
.site-header{position:absolute;left:0;top:0;width:1200px;height:137px;background:var(--white)}
.brand{position:absolute;left:112px;top:32px;width:152px;text-align:center;color:var(--green);font-weight:900}
.brand-name{font-size:44px;line-height:48px;letter-spacing:1px}
.brand-sub{font-size:12px;font-weight:900;letter-spacing:.5px;color:var(--green);margin-top:2px}
.contact-item{position:absolute;top:58px;text-align:center;transform:translateX(-50%);white-space:nowrap}
.contact-item .label{font-size:15px;font-weight:500;color:var(--ink)}
.contact-item .value{font-size:21px;font-weight:700;color:var(--purple);margin-top:4px}
.contact-item .value.small{font-size:15px;font-weight:400;margin-top:6px}
.social{display:flex;gap:16px;justify-content:center;margin-top:10px}
.social span{width:15px;height:15px;border-radius:50%;background:var(--purple)}
.badge-247{position:absolute;left:910px;top:26px;width:240px;text-align:center;white-space:nowrap}
.badge-247 .dot{width:48px;height:48px;border-radius:50%;border:5px solid var(--purple);background:var(--green);margin:0 auto 6px}
.badge-247 .big{font-size:33px;font-weight:900;color:var(--ink);letter-spacing:-.5px}
.badge-247 .big b{font-size:24px}
.badge-247 .tiny{position:absolute;left:128px;top:110px;font-size:8px;font-weight:700;color:var(--ink)}

/* nav */
.main-nav{position:absolute;left:0;top:137px;width:1200px;height:36px;background:var(--purple-nav);border-bottom:2px solid var(--purple)}
.main-nav a{position:absolute;top:0;height:36px;line-height:36px;text-align:center;font-size:14px;font-weight:500;color:var(--white);text-decoration:none;border-right:1px solid #5d4580}
.main-nav a.active{background:var(--green);color:var(--purple)}
.nav-search{position:absolute;left:892px;top:6px;width:240px;height:24px;background:var(--white);font-size:12px;color:var(--muted);padding:4px 8px}
.nav-search svg{position:absolute;right:8px;top:5px}

/* hero */
.hero{position:absolute;left:0;top:173px;width:1200px;height:666px;background:linear-gradient(90deg,#3d3a3a 0%,#6b6660 35%,#9a8f84 60%,#4e4a4c 100%)}
.hero-photo{position:absolute;inset:0}
.hero-copy{position:absolute;left:64px;top:212px;color:var(--white);white-space:nowrap}
.hero-copy .lead{font-family:"Roboto Condensed",sans-serif;font-weight:300;font-size:31px}
.hero-copy h1{font-family:"Roboto Condensed",sans-serif;font-weight:700;font-size:43px;line-height:50px;margin-top:4px}
.hero-copy .values{font-family:"Roboto Condensed",sans-serif;font-weight:700;font-size:33px;color:var(--green);margin-top:8px;letter-spacing:.5px}
.btn-know{position:absolute;left:72px;top:436px;width:192px;height:42px;line-height:42px;text-align:center;background:var(--green);color:var(--purple);font-size:20px;font-weight:500;border-radius:6px}
.dots{position:absolute;left:100px;top:594px;display:flex;gap:10px}
.dots span{width:10px;height:10px;border-radius:50%;border:2px solid var(--white)}
.dots span.on{background:var(--white)}

/* about */
.section-title{position:absolute;left:0;width:1200px;text-align:center;font-weight:700;font-size:32px}
.title-rule{position:absolute;left:570px;width:60px;height:2px}
.about-title{top:936px;color:var(--purple)}
.about-rule{top:996px;background:var(--purple)}
.about-photo{position:absolute;left:126px;top:1036px;width:380px;height:277px;border:2px solid #cfcfcf;border-radius:8px;overflow:hidden;background:var(--white);padding:6px}
.about-photo div{width:100%;height:100%;border-radius:4px;background:linear-gradient(90deg,#8a8e92 0%,#b8b4ad 40%,#c4363d 70%,#a82e36 100%)}
.about-text{position:absolute;left:620px;top:1036px;width:385px;font-size:13.5px;line-height:20px;color:var(--ink)}
.about-text p+p{margin-top:18px}
.btn-pill{position:absolute;height:34px;border-radius:17px;background:var(--purple);color:var(--white);font-size:12px;font-weight:500;line-height:34px;padding-left:24px}
.btn-pill .arrow{position:absolute;right:4px;top:4px;width:26px;height:26px;border-radius:50%;background:var(--green)}
.btn-pill .arrow svg{position:absolute;left:7px;top:6px}

/* services */
.services{position:absolute;left:0;top:1415px;width:1200px;height:1202px;background:var(--purple)}
.services .section-title{top:56px;color:var(--green)}
.services .title-rule{top:114px;background:var(--green)}
.services-intro{position:absolute;left:0;top:158px;width:1200px;text-align:center;color:var(--white);font-size:13.5px;line-height:22px}
.services-intro p+p{margin-top:12px}
.card{position:absolute;width:240px;text-align:center}
.card .thumb{width:240px;height:197px;background:var(--white);border-radius:14px;padding:14px 30px}
.card .thumb div{width:100%;height:100%;border-radius:4px}
.card h3{font-size:17px;font-weight:500;color:var(--green);margin-top:32px}
.card p{font-size:13px;line-height:15px;color:var(--white);margin-top:12px;padding:0 6px}
.card .read{display:inline-block;margin-top:14px;height:24px;line-height:24px;padding:0 14px;background:var(--green);color:var(--purple);font-size:12px;border-radius:3px}

/* contact */
.contact-title{top:2714px;color:var(--ink)}
.form-label{position:absolute;font-size:13px;color:var(--muted)}
.form-label b{color:var(--purple);font-weight:400;margin-left:6px}
.input{position:absolute;border:1px solid var(--line);background:var(--white)}
.req{position:absolute;left:672px;top:2995px;font-size:12px;color:var(--muted)}
.agree{position:absolute;left:676px;top:3032px;font-size:13px;color:var(--muted);display:flex;align-items:center;gap:10px}
.agree span{width:14px;height:14px;border:1px solid var(--line)}

/* newsletter */
.newsletter{position:absolute;left:0;top:3238px;width:1200px;height:152px;background:var(--green)}
.newsletter h2{position:absolute;left:172px;top:61px;font-size:24px;font-weight:700;color:var(--purple)}
.news-input{position:absolute;left:380px;top:53px;width:506px;height:50px;background:var(--white)}
.news-btn{position:absolute;left:886px;top:53px;width:128px;height:50px;background:var(--purple);color:var(--white);font-size:13px;font-weight:700;text-align:center;line-height:50px}

/* footer */
.site-footer{position:absolute;left:0;top:3390px;width:1200px;height:323px;background:var(--purple-deep)}
.foot-brand{position:absolute;left:112px;top:110px;width:154px;text-align:center;color:var(--white);font-weight:900}
.foot-brand .brand-name{font-size:46px;line-height:52px}
.foot-brand .brand-sub{color:var(--white);font-size:13px;margin-top:4px}
.foot-head{position:absolute;top:66px;font-size:16px;font-weight:700;color:var(--green)}
.foot-block{position:absolute;font-size:13px;line-height:19px;color:var(--white)}
.foot-block b{display:block;color:var(--green);font-weight:700}
.foot-links{position:absolute;left:628px;top:118px;font-size:14px;line-height:37px;color:var(--white);list-style:none}
.foot-input{position:absolute;height:36px;background:var(--white);font-size:13px;color:var(--muted);padding:10px 10px;border:1px solid #ddd}
.foot-send{position:absolute;left:830px;top:203px;font-size:15px;font-weight:700;color:var(--white)}
.copyright{position:absolute;left:0;top:3713px;width:1200px;height:76px;background:var(--grey-bar);color:#dddddd;font-size:12px;text-align:center;line-height:76px}
</style>
</head>
<body>

<header class="site-header">
  <div class="brand">
    <div class="brand-name">BROOK</div>
    <div class="brand-sub">REFRIGERATION</div>
  </div>
  <div class="contact-item" style="left:410px">
    <div class="label">Call us</div>
    <div class="value">1-888-555-0142</div>
  </div>
  <div class="contact-item" style="left:610px">
    <div class="label">Email</div>
    <div class="value small">info@brookrefrigeration.com</div>
  </div>
  <div class="contact-item" style="left:813px">
    <div class="label">Follow us</div>
    <div class="social"><span></span><span></span><span></span><span></span></div>
  </div>
  <div class="badge-247">
    <div class="dot"></div>
    <div class="big">24/7 <b>365 DAYS</b></div>
    <div class="tiny">SERVICE AVAILABLE</div>
  </div>
</header>

<nav class="main-nav">
  <a class="active" href="#" style="left:128px;width:124px">HOME</a>
  <a href="#" style="left:252px;width:234px">ABOUT US</a>
  <a href="#" style="left:486px;width:162px">SERVICES</a>
  <a href="#" style="left:648px;width:204px">CONTACT US</a>
  <div class="nav-search">Search
    <svg width="12" height="12" viewBox="0 0 12 12"><circle cx="5" cy="5" r="3.6" fill="none" stroke="#555" stroke-width="1.5"/><line x1="7.6" y1="7.6" x2="11" y2="11" stroke="#555" stroke-width="1.5"/></svg>
  </div>
</nav>

<section class="hero">
  <div class="hero-photo" role="img" aria-label="Refrigeration technician in uniform and cap holding a clipboard in front of a commercial display fridge"></div>
  <div class="hero-copy">
    <div class="lead">Our dedicated team specialises in</div>
    <h1>COMMERCIAL REFRIGERATION &amp;<br>AIR CONDITIONING EQUIPMENT.</h1>
    <div class="values">KNOWLEDGE • EXPERIENCE • PASSION</div>
  </div>
  <div class="btn-know">KNOW MORE</div>
  <div class="dots"><span class="on"></span><span></span><span></span></div>
</section>

<h2 class="section-title about-title">About Brook Refrigeration</h2>
<div class="title-rule about-rule"></div>
<div class="about-photo"><div role="img" aria-label="Technician in red shirt repairing the wiring of an air conditioning unit"></div></div>
<div class="about-text">
  <p>Brook Refrigeration's dedicated team specialises in commercial refrigeration and air conditioning equipment.&nbsp; Based in Harbourton, we cover Northvale Metro and surrounding areas.</p>
  <p>Lorem ipsum dolor sit amet, consectetur adipiscing elit. Morbi auctor ullamcorper congue. Phasellus quis lacus quis ante ornare tincidunt lobortis quis enim. Nam lacinia ex ac quam sollicitudin placerat. Nullam eu laoreet diam. Vivamus sed mattis erat. Cras fringilla maximus magna, eleifend pellentesque tellus</p>
</div>
<div class="btn-pill" style="left:622px;top:1266px;width:136px">READ MORE
  <span class="arrow"><svg width="12" height="14" viewBox="0 0 12 14"><path d="M3 2l6 5-6 5" fill="none" stroke="#40275e" stroke-width="2.4"/></svg></span>
</div>

<section class="services">
  <h2 class="section-title">Our Services</h2>
  <div class="title-rule"></div>
  <div class="services-intro">
    <p>Whether you wish to cool, store or display food and drink, we have a wide range of commercial refrigerator services<br>catering to various small and large scale industries.</p>
    <p>We specialize in wide range of commercial refrigeration operations and maintenance services<br>to ensure efficient functioning of the systems</p>
  </div>

  <div class="card" style="left:131px;top:303px">
    <div class="thumb"><div role="img" aria-label="White commercial chest freezer" style="background:linear-gradient(180deg,#e8eef2,#b9c6cf)"></div></div>
    <h3>Commercial Freezer</h3>
    <p>Lorem ipsum dolor sit amet, consectetur adipiscing elit. Morbi auctor ullamcorper congue. Phasellus quis lacus quis ante ornare tincidunt</p>
    <span class="read">Read more ›</span>
  </div>
  <div class="card" style="left:481px;top:303px">
    <div class="thumb"><div role="img" aria-label="Stainless steel walk in cooler room" style="background:linear-gradient(180deg,#dfe2e4,#a9adb0)"></div></div>
    <h3>Walk In Cooler</h3>
    <p>Lorem ipsum dolor sit amet, consectetur adipiscing elit. Morbi auctor ullamcorper congue. Phasellus quis lacus quis ante ornare tincidunt lobortis quisenim.</p>
    <span class="read">Read more ›</span>
  </div>
  <div class="card" style="left:833px;top:303px">
    <div class="thumb"><div role="img" aria-label="Double glass door kitchen refrigerator" style="background:linear-gradient(180deg,#d8dcdf,#9ea4a8)"></div></div>
    <h3>Kitchen Refrigeration</h3>
    <p>Lorem ipsum dolor sit amet, consectetur adipiscing elit. Morbi auctor ullamcorper congue. Phasellus quis lacus quis ante ornare tincidunt</p>
    <span class="read">Read more ›</span>
  </div>

  <div class="card" style="left:131px;top:740px">
    <div class="thumb"><div role="img" aria-label="Black glass door merchandiser fridge" style="background:linear-gradient(180deg,#2a2f3a,#5b6b80)"></div></div>
    <h3>Glass Door Merchandiser</h3>
    <p>Lorem ipsum dolor sit amet, consectetur adipiscing elit. Morbi auctor ullamcorper congue. Phasellus quis lacus quis ante ornare tincidunt lobortis quisenim.</p>
    <span class="read">Read more ›</span>
  </div>
  <div class="card" style="left:481px;top:740px">
    <div class="thumb"><div role="img" aria-label="Curved glass bakery display case" style="background:linear-gradient(180deg,#e3e7ea,#9aa1a6)"></div></div>
    <h3>Bakery Display Case</h3>
    <p>Lorem ipsum dolor sit amet, consectetur adipiscing elit. Morbi auctor ullamcorper congue. Phasellus quis lacus quis ante ornare tincidunt lobortis quisenim.</p>
    <span class="read">Read more ›</span>
  </div>
  <div class="card" style="left:833px;top:740px">
    <div class="thumb"><div role="img" aria-label="Stainless steel commercial ice machine" style="background:linear-gradient(180deg,#d5d9dc,#8f969b)"></div></div>
    <h3>Ice machines</h3>
    <p>Lorem ipsum dolor sit amet, consectetur adipiscing elit. Morbi auctor ullamcorper congue. Phasellus quis lacus quis ante ornare tincidunt lobortis quisenim.</p>
    <span class="read">Read more ›</span>
  </div>
</section>

<h2 class="section-title contact-title">Contact Us</h2>
<div class="form-label" style="left:152px;top:2826px">Name<b>*</b></div>
<div class="input" style="left:152px;top:2850px;width:396px;height:36px"></div>
<div class="form-label" style="left:152px;top:2910px">Email<b>*</b></div>
<div class="input" style="left:152px;top:2935px;width:396px;height:36px"></div>
<div class="form-label" style="left:152px;top:2996px">Phone</div>
<div class="input" style="left:152px;top:3021px;width:396px;height:36px"></div>
<div class="form-label" style="left:672px;top:2826px">Description</div>
<div class="input" style="left:672px;top:2850px;width:396px;height:131px"></div>
<div class="req">* Required</div>
<div class="agree"><span></span>I have read the Disclaimer and Privacy Policy</div>
<div class="btn-pill" style="left:530px;top:3122px;width:138px;padding-left:32px">SUBMIT
  <span class="arrow"><svg width="12" height="14" viewBox="0 0 12 14"><path d="M3 2l6 5-6 5" fill="none" stroke="#40275e" stroke-width="2.4"/></svg></span>
</div>

<section class="newsletter">
  <h2>NEWSLETTER</h2>
  <div class="news-input"></div>
  <div class="news-btn">SUBSCRIBE</div>
</section>

<footer class="site-footer">
  <div class="foot-brand">
    <div class="brand-name">BROOK</div>
    <div class="brand-sub">REFRIGERATION</div>
  </div>

  <div class="foot-head" style="left:360px">CONTACT US</div>
  <svg class="abs" style="left:356px;top:106px" width="22" height="28" viewBox="0 0 22 28"><path d="M11 1C5.5 1 1.5 5 1.5 10.3 1.5 17 11 27 11 27s9.5-10 9.5-16.7C20.5 5 16.5 1 11 1z" fill="#a4ef68"/><circle cx="11" cy="10.3" r="3.6" fill="#3a2455"/></svg>
  <div class="foot-block" style="left:393px;top:106px"><b>ADDRESS</b>88 Lakeside Drive<br>Harbourton, NV 6027</div>
  <svg class="abs" style="left:356px;top:188px" width="22" height="22" viewBox="0 0 24 24"><path d="M6.6 10.8a15 15 0 0 0 6.6 6.6l2.2-2.2c.3-.3.7-.4 1-.2 1.1.4 2.3.6 3.6.6.6 0 1 .4 1 1V20c0 .6-.4 1-1 1A17 17 0 0 1 3 4c0-.6.4-1 1-1h3.5c.6 0 1 .4 1 1 0 1.3.2 2.5.6 3.6.1.3 0 .7-.2 1z" fill="#a4ef68"/></svg>
  <div class="foot-block" style="left:393px;top:190px"><b>PHONE NUMBER</b>1-888-555-0142</div>

  <div class="foot-head" style="left:626px">ABOUT</div>
  <ul class="foot-links"><li>Home</li><li>About Us</li><li>Services</li><li>Contact us</li></ul>

  <div class="foot-head" style="left:790px">GET IN TOUCH</div>
  <div class="foot-input" style="left:794px;top:106px;width:154px">Name</div>
  <div class="foot-input" style="left:952px;top:106px;width:154px">Phone</div>
  <div class="foot-input" style="left:794px;top:148px;width:312px">Email address</div>
  <div class="foot-send">SEND</div>
</footer>

<div class="copyright">© 2018 brookrefrigeration All Right Reserved</div>

</body>
</html>
```